Photography business - business card design quick turn around

Create a business card design for me please. I actually need the final design back before the end of Sunday 13th May 7pm GMT. Sorry for the short notice.

Photoshop artwork template uploaded with artwork guidelines including printer profiles and other mandatory specifications. Only one side of the business card is required as the other side will be an image.

The design is required as an unflattened PSD file so that I can edit the text if I need to.

My brand colours are white and the teal you see in the logo. Occasionally I also use a dark grey on my website (I don't mind the shade of grey as appreciate grey on teal would be a different grey, to the grey I use on white on the website, so just use a shade of grey that matches). Font can be as the font for the logo or if you prefer I am open to another sans serif, easily legible font. Ideally font size will be 12+.Please do not use capital letters for text. I prefer everything to be lower case, if possible.

Thank you.

Lena

Target Market(s)

Other business owners who may refer me and families

Industry/Entity Type

Photographer

Contact Information for Business Card

Silver Kettle Photography Logo
Sub text: family portraiture, captured with love

Contact information, ideally using simple icons to represent email / website / facebook / instagram / pinterest

email: lena@silverkettlephotography.co.uk
website: silverkettlephotography.co.uk
facebook: @silverkettlephotography
pinterest: pinterest.com/silverkettlepho
instagram: @silverkettle_photography
mobile/telephone: 07713460291

If there is too much text then please drop the instagram and pinterest information.

Font styles to use
Sans Serif

Colors
33b8a4

Requirements
Must have
• Logo
• Contact details as listed above
• sub text
Nice to have
• Instagram and Pinterest contact details
• Nice to have icons to represent website / phone / facebook etc followered by the handle where relevant

```html
<!DOCTYPE html>
<html lang="en">
<head>
<meta charset="utf-8">
<title>Silver Kettle Photography – Business Card</title>
<link rel="stylesheet" href="https://fonts.googleapis.com/css2?family=Arimo:wght@400&family=Crimson+Text:ital@1&display=swap">
<style>
  :root {
    --teal: #33b8a4;
    --card-white: #f7f7f7;
    --ink: #1e1e1e;
    --backdrop: #2a2a2a;
    --icon-fill: #ffffff;
  }
  * { box-sizing: border-box; margin: 0; padding: 0; }
  html, body {
    width: 1200px;
    height: 997px;
    overflow: hidden;
    background: var(--backdrop);
  }
  .stage {
    width: 1200px;
    height: 997px;
    display: flex;
    align-items: center;
    justify-content: center;
  }
  .business-card {
    position: relative;
    width: 840px;
    height: 480px;
    background: var(--card-white);
    border-radius: 22px;
    overflow: hidden;
    font-family: "Arimo", Arial, sans-serif;
    color: var(--ink);
  }
  .tagline-band {
    position: absolute;
    left: 0; top: 0; bottom: 0;
    width: 72px;
    background: var(--teal);
    display: flex;
    align-items: center;
    justify-content: center;
  }
  .tagline {
    transform: rotate(-90deg);
    white-space: nowrap;
    font-family: "Crimson Text", Georgia, serif;
    font-style: italic;
    font-size: 26px;
    color: var(--ink);
  }
  .brand-name {
    position: absolute;
    left: 72px; right: 0;
    top: 150px;
    text-align: center;
    font-size: 40px;
    font-weight: 400;
    color: var(--teal);
    letter-spacing: 0.5px;
  }
  .contact-list {
    position: absolute;
    left: 100px;
    bottom: 42px;
    list-style: none;
    display: flex;
    flex-direction: column;
    gap: 12px;
  }
  .social-list {
    position: absolute;
    right: 40px;
    top: 250px;
    list-style: none;
    display: flex;
    flex-direction: column;
    align-items: flex-end;
    gap: 10px;
  }
  .contact-item, .social-item {
    display: flex;
    align-items: center;
    gap: 10px;
    font-size: 22px;
    line-height: 1;
  }
  .social-item { flex-direction: row-reverse; }
  .icon-badge {
    width: 22px; height: 22px;
    flex: none;
  }
  .social-dot {
    width: 18px; height: 18px;
    border-radius: 50%;
    background: var(--teal);
    flex: none;
  }
</style>
</head>
<body>
<main class="stage">
  <article class="business-card">
    <aside class="tagline-band">
      <p class="tagline">family portraiture, captured with love</p>
    </aside>

    <h1 class="brand-name">silver kettle photography</h1>

    <ul class="social-list">
      <li class="social-item"><span class="social-dot"></span><span>silverkettlephotography</span></li>
      <li class="social-item"><span class="social-dot"></span><span>silverkettlepho</span></li>
      <li class="social-item"><span class="social-dot"></span><span>silverkettle_photography</span></li>
    </ul>

    <ul class="contact-list">
      <li class="contact-item">
        <svg class="icon-badge" viewBox="0 0 22 22" aria-hidden="true">
          <circle cx="11" cy="11" r="11" fill="var(--teal)"/>
          <rect x="7.5" y="5" width="7" height="12" rx="1.5" fill="none" stroke="var(--icon-fill)" stroke-width="1.5"/>
          <line x1="10" y1="15" x2="12" y2="15" stroke="var(--icon-fill)" stroke-width="1.2"/>
        </svg>
        <span>07713460291</span>
      </li>
      <li class="contact-item">
        <svg class="icon-badge" viewBox="0 0 22 22" aria-hidden="true">
          <circle cx="11" cy="11" r="11" fill="var(--teal)"/>
          <rect x="5.5" y="7" width="11" height="8" rx="1" fill="none" stroke="var(--icon-fill)" stroke-width="1.4"/>
          <polyline points="5.5,7.5 11,11.5 16.5,7.5" fill="none" stroke="var(--icon-fill)" stroke-width="1.4"/>
        </svg>
        <span>lena@silverkettlephotography.co.uk</span>
      </li>
      <li class="contact-item">
        <svg class="icon-badge" viewBox="0 0 22 22" aria-hidden="true">
          <circle cx="11" cy="11" r="11" fill="var(--teal)"/>
          <path d="M11 4.5a4 4 0 0 1 4 4c0 3-4 8-4 8s-4-5-4-8a4 4 0 0 1 4-4z" fill="var(--icon-fill)"/>
          <circle cx="11" cy="8.5" r="1.5" fill="var(--teal)"/>
        </svg>
        <span>silverkettlephotography.co.uk</span>
      </li>
    </ul>
  </article>
</main>
</body>
</html>
```